Business Card Design Project

This is the first time we use our new logo. We need a business card that we can use both on our institutional corporate relationships and also that works for our staff that deals with consumers directly.

VELUNDA is a new company dedicated to empower consumers and to provide them with the best choices for specialized health care using the latest telemedicine technology (medicine at a distance via videoconference).

We want to print this cards in high quality materials and process. We will like designs that allow us to use UV spot varnish and other techniques that will differentiate us.

We are including Two different versions of Color logos. In addition we are including white over black background logos. Those can be used replacing the black for a color.

Please note this is the first time we will be creating any corporate materials with our new logo and colors.

Target Market(s)

34+ consumers of medium high and high socioeconomic levels.

Industry/Entity Type

Health

Requirements
Must have
• Our logo on its original colors
Should not have
• Any other graphical element or design that is not our logo

```html
<!DOCTYPE html>
<html lang="en">
<head>
<meta charset="utf-8">
<title>VELUNDA Business Card</title>
<link rel="stylesheet" href="https://fonts.googleapis.com/css2?family=Montserrat:wght@600;700&family=Arimo:wght@400&display=swap">
<style>
  :root {
    --page-bg: #e6e8ec;
    --card-white: #ffffff;
    --sky: #58b4de;
    --royal: #1c6db4;
    --navy: #1d4f7e;
    --brand-ink: #1f5886;
    --text-ink: #1c1c1c;
    --divider: #c8c8c8;
  }
  * { box-sizing: border-box; margin: 0; padding: 0; }
  html, body { width: 1200px; height: 987px; overflow: hidden; }
  body { background: var(--page-bg); position: relative; font-family: "Arimo", Arial, sans-serif; }

  .card {
    position: absolute;
    border-radius: 22px;
    overflow: hidden;
    box-shadow: 0 6px 18px rgba(0,0,0,.12);
  }

  /* Back side */
  .card-back {
    left: 560px; top: 80px; width: 580px; height: 331px;
    background: var(--sky);
  }
  .card-back .brand {
    position: absolute; left: 0; right: 0; top: 120px;
    display: flex; align-items: center; justify-content: center; gap: 14px;
    font-family: "Montserrat", sans-serif; font-weight: 700;
    font-size: 40px; letter-spacing: 3px; color: var(--card-white);
  }
  .card-back .brand-dot {
    width: 30px; height: 30px; border-radius: 50%;
    border: 5px solid var(--card-white);
  }
  .card-back .web {
    position: absolute; left: 0; right: 0; top: 220px; text-align: center;
    font-size: 19px; letter-spacing: 4px; color: var(--card-white);
  }

  /* Front side */
  .card-front {
    left: 60px; top: 470px; width: 700px; height: 400px;
    background: var(--card-white);
  }
  .card-front .swoosh { position: absolute; inset: 0; }
  .card-front .brand {
    position: absolute; left: 60px; top: 40px;
    display: flex; align-items: center; gap: 16px;
    font-family: "Montserrat", sans-serif; font-weight: 700;
    font-size: 54px; letter-spacing: 3px; color: var(--brand-ink);
  }
  .card-front .brand-dot {
    width: 40px; height: 40px; border-radius: 50%;
    border: 6px solid var(--brand-ink);
  }
  .address {
    position: absolute; left: 40px; top: 142px; width: 250px;
    text-align: right; font-style: normal;
    font-size: 17px; line-height: 25px; color: var(--text-ink);
  }
  .column-divider {
    position: absolute; left: 310px; top: 140px; width: 1px; height: 96px;
    background: var(--divider);
  }
  .contacts {
    position: absolute; left: 328px; top: 140px; list-style: none;
    font-size: 19px; line-height: 26px; color: var(--text-ink);
  }
  .contacts li { display: flex; align-items: center; gap: 8px; }
  .contacts svg { width: 15px; height: 15px; flex: none; }
  .holder {
    position: absolute; right: 36px; bottom: 26px;
    color: var(--card-white); font-family: "Montserrat", sans-serif;
  }
  .holder .name { font-weight: 700; font-size: 30px; }
  .holder .title { font-family: "Arimo", sans-serif; font-size: 24px; }
</style>
</head>
<body>

<section class="card card-back">
  <div class="brand"><span class="brand-dot"></span>VELUNDA</div>
  <p class="web">www.velunda.com</p>
</section>

<section class="card card-front">
  <svg class="swoosh" viewBox="0 0 700 400" preserveAspectRatio="none" aria-hidden="true">
    <path d="M0,292 C220,296 440,304 700,312 L700,400 L0,400 Z" fill="var(--sky)"/>
    <path d="M0,264 C220,270 440,282 700,296 L700,306 C440,298 220,288 0,284 Z" fill="var(--royal)"/>
    <path d="M0,256 C220,262 440,274 700,288" fill="none" stroke="var(--navy)" stroke-width="3"/>
  </svg>

  <div class="brand"><span class="brand-dot"></span>VELUNDA</div>

  <address class="address">
    Street Name<br>City Name<br>State, City Zip Code
  </address>
  <div class="column-divider"></div>

  <ul class="contacts">
    <li><svg viewBox="0 0 16 16"><circle cx="8" cy="8" r="7" fill="none" stroke="#222" stroke-width="1.4"/><path d="M5.5 4.5 L7 6 L6 7.2 Q7 9 8.8 10 L10 9 L11.5 10.5 L10.5 11.6 Q7 11.5 4.4 7 Z" fill="#222"/></svg>012-555-0148</li>
    <li><svg viewBox="0 0 16 16"><circle cx="8" cy="8" r="7" fill="none" stroke="#222" stroke-width="1.4"/><path d="M5.5 4.5 L7 6 L6 7.2 Q7 9 8.8 10 L10 9 L11.5 10.5 L10.5 11.6 Q7 11.5 4.4 7 Z" fill="#222"/></svg>012-555-0148</li>
    <li><svg viewBox="0 0 16 16"><rect x="1" y="3.5" width="14" height="9.5" fill="#222"/><path d="M1.5 4 L8 9 L14.5 4" fill="none" stroke="#fff" stroke-width="1.3"/></svg>name@velunda.com</li>
    <li><svg viewBox="0 0 16 16"><circle cx="8" cy="8" r="6.5" fill="none" stroke="#222" stroke-width="1.3"/><ellipse cx="8" cy="8" rx="3" ry="6.5" fill="none" stroke="#222" stroke-width="1"/><path d="M1.5 8 H14.5 M2.5 5 H13.5 M2.5 11 H13.5" stroke="#222" stroke-width="1"/></svg>www.velunda.com</li>
  </ul>

  <p class="holder"><span class="name">Your Name,</span><span class="title">Title</span></p>
</section>

</body>
</html>
```